Belmont Ridge Business Card Design Project

We have recently rebranded and would like to design new business cards that incorporate the corporate logo - double sided cards with corporate logo on one side and contact details on the other

Target Market(s)

Sophisticated and high net worth investors and finance industry professionals

Industry/Entity Type

Funds Management

Contact Information for Business Card

The card should prominently feature the company name and logo. Other details will be standard contact details for each staff member - name, address, phone, email, website

Colors
0054AA
0677BA
7BADD7
CADEEF
E8F1F8

Requirements
Must have
• Double-sided design with one side prominently featuring the corporate logo and the other side with all standard contact details

```html
<!DOCTYPE html>
<html lang="en">
<head>
<meta charset="utf-8">
<title>Belmont Ridge – Business Card</title>
<link rel="stylesheet" href="https://fonts.googleapis.com/css2?family=Cinzel:wght@500;600&family=Arimo:wght@400&display=swap">
<style>
  :root{
    --stage:#262626;
    --navy:#1f4471;
    --paper:#ffffff;
    --ink-light:#ffffff;
  }
  *{margin:0;padding:0;box-sizing:border-box}
  html,body{width:1075px;height:1200px;overflow:hidden;background:var(--stage)}
  .stage{position:relative;width:1075px;height:1200px}
  .card{position:absolute;left:206px;width:663px;height:395px;box-shadow:3px 3px 4px rgba(0,0,0,.6);overflow:hidden}
  .card--front{top:187px;background:var(--paper)}
  .card--back{top:637px;background:var(--navy)}

  .wordmark{position:absolute;font-family:"Cinzel",serif;font-weight:600;white-space:nowrap;letter-spacing:.5px}
  .card--front .wordmark{right:41px;top:124px;font-size:44px;color:var(--navy)}
  .card--back .wordmark{left:0;right:0;text-align:center;top:226px;font-size:58px;color:var(--ink-light)}

  .person{position:absolute;left:35px;top:222px;color:var(--navy)}
  .person__name{font-family:"Cinzel",serif;font-weight:500;font-size:25px;line-height:1.1}
  .person__role{font-family:"Arimo",sans-serif;font-size:16.5px;line-height:1}

  .contact-band{position:absolute;left:0;right:0;bottom:0;height:116px;background:var(--navy);color:var(--ink-light);font-family:"Arimo",sans-serif;font-size:17.5px}
  .contact-list{position:absolute;left:35px;top:22px;list-style:none}
  .contact-list li{display:flex;align-items:center;height:24px}
  .contact-list svg{width:17px;height:17px;margin-right:6px;fill:none;stroke:var(--ink-light);stroke-width:1.6}
  .address{position:absolute;right:41px;top:50px;text-align:right;line-height:24px;font-style:normal}

  .web-rule{position:absolute;left:0;right:0;top:328px;display:flex;align-items:center;justify-content:center;color:var(--ink-light);font-family:"Arimo",sans-serif;font-size:17.5px}
  .web-rule::before,.web-rule::after{content:"";width:148px;height:1px;background:var(--ink-light)}
  .web-rule span{padding:0 6px}
</style>
</head>
<body>
<main class="stage">
  <section class="card card--front">
    <div class="wordmark">Belmont Ridge</div>
    <div class="person">
      <div class="person__name">DANIEL HARTLEY</div>
      <div class="person__role">MANAGING DIRECTOR</div>
    </div>
    <div class="contact-band">
      <ul class="contact-list">
        <li><svg viewBox="0 0 20 20"><path d="M5 2l3 4-2 2c1 2 3 4 5 5l2-2 4 3-2 3C9 17 3 11 2 5z"/></svg>044-987 654 321</li>
        <li><svg viewBox="0 0 20 20"><rect x="2" y="5" width="16" height="11"/><path d="M2 5l8 6 8-6"/></svg>hello@belmontridge.com</li>
        <li><svg viewBox="0 0 20 20"><circle cx="10" cy="10" r="8"/><ellipse cx="10" cy="10" rx="3.5" ry="8"/><path d="M2 10h16M3.5 6h13M3.5 14h13"/></svg>www.belmontridge.com</li>
      </ul>
      <address class="address">421, Address line goes here<br>45452, Country Name</address>
    </div>
  </section>

  <section class="card card--back">
    <div class="wordmark">Belmont Ridge</div>
    <div class="web-rule"><span>www.belmontridge.com</span></div>
  </section>
</main>
</body>
</html>
```